Baby Organic Coconut Body Lotion

Meadow Hush Naturals is developing a line of Organic and Natural skin care products for babies and toddlers, although our skin care can also be used by adults too. These products include a body lotion, shampoo & body wash, powder, hair cream, massage body oil, bath soak, baby balm, Bar Soap, gift box and many more.
This will be an ever expanding line so the list will go on and on. We are looking forward for an eye catching designs. I attached some of our current label designs and product images. Also, we have different Baby organic body lotion and Baby organic shampoo & body wash with different fruit flavours. Coconut lotion will share the same design with the shampoo & body wash. I would like you to start with the coconut design. I have uploaded plastic bottles with different colourful caps. The bottle with the white cap is for the coconut design. the bottle with the red cap is for the strawberry design. the bottle with the orange cap is for the orange design. the bottle with the yellow cap is for the pineapple design. the bottle with the green cap is for the apple design. Bear in my mind that my baby organic skin care are made with different fruit flavours.
Target Market(s)
My target market are for mothers that wants to buy there baby and toddler skin care products.
Industry/Entity Type
Baby
Look and feel

```html
<!DOCTYPE html>
<html lang="en">
<head>
<meta charset="UTF-8">
<title>Meadow Hush Naturals – Skin Care Label Range</title>
<link rel="stylesheet" href="https://fonts.googleapis.com/css2?family=Saira+Semi+Condensed:wght@400;500&display=swap">
<style>
  :root {
    --page-bg: #d8e3e8;
    --label-bg: #e4e5e3;
    --brand-ink: #c75aa6;
    --brand-dot: #6fc9e6;

    --coconut-title: #3a3026;
    --coconut-band-a: #5a4b3b;
    --coconut-band-b: #3d3227;
    --coconut-photo-a: #f1eee8;
    --coconut-photo-b: #6b4a2c;

    --apple-title: #a9cf5c;
    --apple-band-a: #cfe79a;
    --apple-band-b: #78b532;
    --apple-photo-a: #c9e49a;
    --apple-photo-b: #6fae2c;

    --strawberry-title: #d81f52;
    --strawberry-band-a: #ef1f86;
    --strawberry-band-b: #c81d25;
    --strawberry-photo-a: #f05a6a;
    --strawberry-photo-b: #b5121f;

    --pineapple-title: #d3c95e;
    --pineapple-band-a: #e2da78;
    --pineapple-band-b: #a88e2b;
    --pineapple-photo-a: #f7e35a;
    --pineapple-photo-b: #9a7a2e;

    --orange-title: #e9a11b;
    --orange-band-a: #f6d21c;
    --orange-band-b: #ee761b;
    --orange-photo-a: #f8c22a;
    --orange-photo-b: #ef8a14;
  }

  * { box-sizing: border-box; margin: 0; padding: 0; }

  html, body {
    width: 1200px;
    height: 944px;
    overflow: hidden;
    background: var(--page-bg);
    font-family: "Saira Semi Condensed", "Arial Narrow", sans-serif;
  }

  .label-range {
    position: absolute;
    top: 287px;
    left: 44px;
    display: flex;
    gap: 28px;
  }

  .label {
    width: 200px;
    height: 370px;
    background: var(--label-bg);
    display: flex;
    flex-direction: column;
    align-items: center;
    overflow: hidden;
    box-shadow: 0 2px 8px rgba(60, 80, 90, 0.18);
  }

  .brand {
    margin-top: 22px;
    height: 44px;
    display: flex;
    align-items: center;
    gap: 7px;
    color: var(--brand-ink);
    font-weight: 500;
    font-size: 14px;
    white-space: nowrap;
  }

  .brand-dot {
    width: 10px;
    height: 10px;
    border-radius: 50%;
    background: var(--brand-dot);
  }

  .title-block {
    height: 78px;
    width: 100%;
    padding: 0 10px;
    display: flex;
    flex-direction: column;
    align-items: center;
    justify-content: flex-end;
  }

  .product-name {
    font-weight: 400;
    font-size: 34px;
    line-height: 1;
    white-space: nowrap;
    max-width: 100%;
    color: var(--title);
  }

  .label--apple .product-name { font-size: 38px; }
  .label--strawberry .product-name { font-size: 25px; }
  .label--pineapple .product-name { font-size: 28px; }
  .label--orange .product-name { font-size: 35px; }

  .product-type {
    margin-top: 6px;
    font-size: 12px;
    line-height: 1;
    color: var(--title);
    white-space: nowrap;
  }

  .claim-band {
    margin-top: 12px;
    width: 100%;
    height: 26px;
    display: flex;
    align-items: center;
    justify-content: center;
    font-size: 14px;
    color: #ffffff;
    white-space: nowrap;
    background: linear-gradient(90deg, var(--band-a), var(--band-b));
  }

  .fruit-photo {
    margin-top: auto;
    width: 100%;
    height: 150px;
    background: linear-gradient(120deg, var(--photo-a), var(--photo-b));
  }

  .label--coconut {
    --title: var(--coconut-title);
    --band-a: var(--coconut-band-a);
    --band-b: var(--coconut-band-b);
    --photo-a: var(--coconut-photo-a);
    --photo-b: var(--coconut-photo-b);
  }
  .label--apple {
    --title: var(--apple-title);
    --band-a: var(--apple-band-a);
    --band-b: var(--apple-band-b);
    --photo-a: var(--apple-photo-a);
    --photo-b: var(--apple-photo-b);
  }
  .label--strawberry {
    --title: var(--strawberry-title);
    --band-a: var(--strawberry-band-a);
    --band-b: var(--strawberry-band-b);
    --photo-a: var(--strawberry-photo-a);
    --photo-b: var(--strawberry-photo-b);
  }
  .label--pineapple {
    --title: var(--pineapple-title);
    --band-a: var(--pineapple-band-a);
    --band-b: var(--pineapple-band-b);
    --photo-a: var(--pineapple-photo-a);
    --photo-b: var(--pineapple-photo-b);
  }
  .label--orange {
    --title: var(--orange-title);
    --band-a: var(--orange-band-a);
    --band-b: var(--orange-band-b);
    --photo-a: var(--orange-photo-a);
    --photo-b: var(--orange-photo-b);
  }
</style>
</head>
<body>
  <main class="label-range">
    <section class="label label--coconut">
      <div class="brand"><span class="brand-dot"></span>Meadow Hush Naturals</div>
      <div class="title-block">
        <h2 class="product-name">COCONUT</h2>
        <p class="product-type">SKIN CARE</p>
      </div>
      <div class="claim-band">Organic and Natural</div>
      <div class="fruit-photo" role="img" aria-label="Photo of a halved coconut showing white flesh and brown husk"></div>
    </section>

    <section class="label label--apple">
      <div class="brand"><span class="brand-dot"></span>Meadow Hush Naturals</div>
      <div class="title-block">
        <h2 class="product-name">APPLE</h2>
        <p class="product-type">SKIN CARE</p>
      </div>
      <div class="claim-band">Organic and Natural</div>
      <div class="fruit-photo" role="img" aria-label="Photo of green apples, one cut in half, with a leaf"></div>
    </section>

    <section class="label label--strawberry">
      <div class="brand"><span class="brand-dot"></span>Meadow Hush Naturals</div>
      <div class="title-block">
        <h2 class="product-name">STRAWBERRY</h2>
        <p class="product-type">SKIN CARE</p>
      </div>
      <div class="claim-band">Organic and Natural</div>
      <div class="fruit-photo" role="img" aria-label="Photo of fresh red strawberries with green leaves"></div>
    </section>

    <section class="label label--pineapple">
      <div class="brand"><span class="brand-dot"></span>Meadow Hush Naturals</div>
      <div class="title-block">
        <h2 class="product-name">PINEAPPLE</h2>
        <p class="product-type">SKIN CARE</p>
      </div>
      <div class="claim-band">Organic and Natural</div>
      <div class="fruit-photo" role="img" aria-label="Photo of a pineapple with sliced yellow wedges"></div>
    </section>

    <section class="label label--orange">
      <div class="brand"><span class="brand-dot"></span>Meadow Hush Naturals</div>
      <div class="title-block">
        <h2 class="product-name">ORANGE</h2>
        <p class="product-type">SKIN CARE</p>
      </div>
      <div class="claim-band">Organic and Natural</div>
      <div class="fruit-photo" role="img" aria-label="Photo of a whole orange and a halved orange with a leaf"></div>
    </section>
  </main>
</body>
</html>
```